Dynamic Business Card for Sports Supplements Company

Hi! I'm looking for an awesome business card to match my existing sports supplement company. I have uploaded my current company logo and screenshot of the front page of my website.

I would like to have something dynamic and interesting and utilize the colors in the website - the reds and purples

The business card should be double sided and focus on a unique eye-catching design on the back and include all the relevant company info.

Most importantly, it should say somewhere: "Sign up on our website for a coupon code."

Target Market(s)

Mostly for women gym goers but it shouldn't be too feminine. It should be in keeping with the website design. It should flow and clearly be connected to it

Industry/Entity Type

Business

Contact Information for Business Card

Lorraine K. Vestal
CEO
LVestal@Quorvanexco.com
www.quorvanexco.com
555.417.3820
P.O. Box 47315
Ashvale, Oregon 00000

Sign up on our website for a coupon code

Font styles to use
Serif
Sans Serif
Other font styles liked:
• Novecento font family and "Quorvanex" is in AR Destine font

Requirements
Must have
• One side should be a bold Quorvanex logo design. Even just the symbol itself may be o.k. (see attached file)

```html
<!DOCTYPE html>
<html lang="en">
<head>
<meta charset="utf-8">
<title>Quorvanex Business Card</title>
<link href="https://fonts.googleapis.com/css2?family=Open+Sans:ital,wght@0,400;0,600;0,700;1,400&display=swap" rel="stylesheet">
<style>
  :root {
    --page: #e9e7e4;
    --card-black: #050505;
    --brand-red: #ed1c24;
    --pattern-red: #ee2a33;
    --white: #ffffff;
    --rule: #cfcfcf;
    --text-light: #f2f2f2;
  }
  html, body {
    margin: 0;
    padding: 0;
    width: 1200px;
    height: 987px;
    overflow: hidden;
    background: var(--page);
    font-family: "Open Sans", Arial, sans-serif;
  }
  .canvas {
    position: relative;
    width: 1200px;
    height: 987px;
  }
  .card {
    position: absolute;
    left: 293px;
    width: 615px;
    height: 352px;
    overflow: hidden;
    box-shadow: 0 3px 10px rgba(0,0,0,0.25);
  }
  .card-front {
    top: 130px;
    background: var(--card-black);
    color: var(--text-light);
  }
  .card-back {
    top: 506px;
    background: var(--brand-red);
  }

  /* front */
  .brand-lockup {
    position: absolute;
    right: 33px;
    top: 118px;
    display: flex;
    align-items: center;
    gap: 10px;
  }
  .brand-mark {
    width: 16px;
    height: 16px;
    background: var(--brand-red);
  }
  .brand-name {
    font-weight: 700;
    font-size: 28px;
    letter-spacing: 1px;
    color: var(--white);
    text-transform: uppercase;
    line-height: 1;
  }
  .holder-name {
    position: absolute;
    left: 30px;
    top: 186px;
    margin: 0;
    font-size: 21px;
    font-weight: 600;
    color: var(--brand-red);
  }
  .holder-title {
    position: absolute;
    left: 30px;
    top: 215px;
    margin: 0;
    font-size: 15px;
    color: var(--text-light);
  }
  .divider {
    position: absolute;
    left: 30px;
    top: 245px;
    width: 555px;
    height: 1px;
    background: var(--rule);
  }
  .contact-list {
    position: absolute;
    left: 30px;
    top: 254px;
    margin: 0;
    padding: 0;
    list-style: none;
    font-size: 15px;
    line-height: 23px;
  }
  .contact-list li {
    display: flex;
    align-items: center;
    gap: 8px;
  }
  .contact-list svg {
    width: 13px;
    height: 13px;
    fill: var(--brand-red);
  }
  .postal-address {
    position: absolute;
    right: 31px;
    top: 254px;
    margin: 0;
    font-style: normal;
    font-size: 15px;
    line-height: 23px;
    text-align: right;
  }
  .footer-band {
    position: absolute;
    left: 0;
    bottom: 0;
    width: 615px;
    height: 24px;
  }
  .website {
    position: absolute;
    left: 30px;
    bottom: 3px;
    font-size: 15px;
    color: var(--white);
  }

  /* back */
  .back-pattern {
    position: absolute;
    inset: 0;
    background: linear-gradient(180deg, var(--pattern-red), var(--brand-red));
  }
  .back-lockup {
    position: absolute;
    left: 378px;
    width: 200px;
    top: 208px;
    text-align: center;
    font-weight: 700;
    font-size: 24px;
    letter-spacing: 1px;
    color: var(--white);
    text-transform: uppercase;
    line-height: 1;
  }
  .coupon-note {
    position: absolute;
    left: 328px;
    width: 300px;
    top: 264px;
    margin: 0;
    text-align: center;
    font-style: italic;
    font-size: 16.5px;
    line-height: 24px;
    color: var(--white);
  }
</style>
</head>
<body>
<main class="canvas">

  <section class="card card-front" aria-label="Business card front">
    <div class="brand-lockup">
      <span class="brand-mark"></span>
      <span class="brand-name">Quorvanex</span>
    </div>

    <h1 class="holder-name">Lorraine K. Vestal</h1>
    <p class="holder-title">CEO</p>
    <div class="divider"></div>

    <ul class="contact-list">
      <li>
        <svg viewBox="0 0 24 24" aria-hidden="true"><path d="M6.6 10.8a15.1 15.1 0 0 0 6.6 6.6l2.2-2.2a1 1 0 0 1 1-.25 11.4 11.4 0 0 0 3.6.57 1 1 0 0 1 1 1V20a1 1 0 0 1-1 1A17 17 0 0 1 3 4a1 1 0 0 1 1-1h3.5a1 1 0 0 1 1 1c0 1.25.2 2.45.57 3.57a1 1 0 0 1-.25 1z"/></svg>
        555.417.3820
      </li>
      <li>
        <svg viewBox="0 0 24 24" aria-hidden="true"><path d="M2 5h20v2l-10 7L2 7z"/><path d="M2 9l10 7 10-7v10H2z"/></svg>
        LVestal@Quorvanexco.com
      </li>
    </ul>

    <address class="postal-address">
      P.O. Box 47315<br>
      Ashvale, Oregon 00000
    </address>

    <svg class="footer-band" viewBox="0 0 615 24" aria-hidden="true">
      <polygon points="0,0 452,0 474,24 0,24" fill="var(--brand-red)"/>
      <polygon points="489,24 512,0 615,0 615,24" fill="var(--white)"/>
    </svg>
    <span class="website">www.quorvanexco.com</span>
  </section>

  <section class="card card-back" aria-label="Business card back">
    <div class="back-pattern" role="img" aria-label="Repeating red chevron pattern background"></div>
    <div class="back-lockup">Quorvanex</div>
    <p class="coupon-note">Sign up on our website<br>for a coupon code</p>
  </section>

</main>
</body>
</html>
```